32 x 24 Swinging Real Estate Yard Sign

We are looking to design a new sign for our business to focus on the remodeling of homes to sell. We are looking to have a yard sign that gets peoples attention and is informational. The headline will be "The Secret to Top Dollar? Remodel First.". We remodel homes for sellers with no up front cost, as they simply pay at closing. This link has more info, https://bramblecresthomes.com/Remodel
The message we want to convey to those seeing the sign is we are a one stop shop, who can renovate your home and sell it for no stress. We are licensed real estate agents and licensed contractors.
Both of these license numbers and info need to be on the design:
CADRE #02794613
Contractors License #1178524
Email: info@bramblecresthomes.com
Phone: (408)614-2907
I'll attach a sample sign we have for our agents normally as well as all brand art work.
• Pantone Colors
o #172A41
Dark blue
o #4381B1
Medium blue
o #6FA6CC
Light blue
Target Market(s)
Residential Real Estate Sellers
Industry/Entity Type
Real Estate
Colors
Designer to choose colors to be used in the design.

```html
<!DOCTYPE html>
<html lang="en">
<head>
<meta charset="utf-8">
<title>Bramblecrest Homes – Remodel First Yard Sign</title>
<link rel="stylesheet" href="https://fonts.googleapis.com/css2?family=League+Spartan:wght@400;700;800&family=Poppins:wght@600;700&display=swap">
<style>
  :root {
    --navy: #172A41;
    --steel: #3A6890;
    --medium: #4381B1;
    --light: #6FA6CC;
    --white: #FFFFFF;
    --panel-shade: #EEF0F3;
  }
  * { margin: 0; padding: 0; box-sizing: border-box; }
  html, body { width: 916px; height: 1200px; overflow: hidden; background: var(--navy); }
  .sign {
    position: relative;
    width: 916px; height: 1200px;
    background: var(--navy);
    font-family: "League Spartan", sans-serif;
    color: var(--navy);
  }
  .sign__panel {
    position: absolute;
    left: 46px; right: 46px; top: 41px; height: 763px;
    background:
      radial-gradient(ellipse at 50% 55%, #FFFFFF 0%, #FFFFFF 45%, var(--panel-shade) 100%);
  }
  .brand {
    position: absolute; left: 0; right: 0; top: 74px;
    text-align: center;
  }
  .brand__dot {
    display: block; margin: 0 auto 26px;
    width: 62px; height: 62px; border-radius: 50%;
    background: var(--medium);
  }
  .brand__name {
    font-weight: 700; font-size: 52px; line-height: 1;
    letter-spacing: 0.01em; color: var(--navy);
  }
  .brand__tagline {
    margin-top: 12px;
    font-weight: 700; font-size: 16px; line-height: 1;
    letter-spacing: 0.42em; color: var(--navy);
  }
  .headline {
    position: absolute; left: 0; right: 0; top: 322px;
    text-align: center; line-height: 1;
  }
  .headline__intro {
    font-weight: 400; font-size: 45px; letter-spacing: -0.01em;
  }
  .headline__intro strong { font-weight: 800; }
  .headline__question {
    margin-top: 4px;
    font-weight: 800; font-size: 72px; letter-spacing: -0.01em;
  }
  .headline__question .accent { color: var(--steel); }
  .headline__remodel {
    margin-top: 10px;
    font-weight: 800; font-size: 128px; letter-spacing: -0.01em;
    color: var(--steel);
  }
  .headline__first {
    margin-top: 4px;
    font-weight: 800; font-size: 228px; letter-spacing: -0.005em;
    line-height: 0.92;
    color: var(--navy);
  }
  .phone-band {
    position: absolute; left: 46px; right: 46px; top: 804px; height: 111px;
    background: var(--steel);
    display: flex; align-items: center; justify-content: center; gap: 8px;
  }
  .phone-band__icon { width: 72px; height: 72px; flex: none; }
  .phone-band__number {
    font-family: "Poppins", sans-serif; font-weight: 700;
    font-size: 74px; line-height: 1; color: var(--white);
    letter-spacing: -0.01em; padding-top: 6px;
  }
  .email {
    position: absolute; left: 0; right: 0; top: 936px;
    display: flex; align-items: center; justify-content: center; gap: 14px;
    font-family: "Poppins", sans-serif; font-weight: 700;
    font-size: 37px; line-height: 1; color: var(--white);
  }
  .email__icon { width: 34px; height: 26px; flex: none; }
  .license {
    position: absolute; height: 47px;
    display: flex; border-radius: 24px; overflow: hidden;
    font-family: "Poppins", sans-serif; font-weight: 700;
    font-size: 27px; line-height: 47px; color: var(--white);
  }
  .license__label { background: var(--steel); padding: 0 16px 0 22px; }
  .license__number { background: var(--medium); padding: 0 22px 0 14px; }
  .license--cadre { left: 291px; top: 1009px; }
  .license--contractor { left: 171px; top: 1067px; }
</style>
</head>
<body>
  <main class="sign">
    <section class="sign__panel">
      <div class="brand">
        <span class="brand__dot"></span>
        <div class="brand__name">BRAMBLECREST</div>
        <div class="brand__tagline">HOMES</div>
      </div>
      <h1 class="headline">
        <div class="headline__intro">THE <strong>SECRET</strong> TO</div>
        <div class="headline__question">TOP <span class="accent">DOLLAR?</span></div>
        <div class="headline__remodel">REMODEL</div>
        <div class="headline__first">FIRST</div>
      </h1>
    </section>

    <div class="phone-band">
      <svg class="phone-band__icon" viewBox="0 0 72 72" aria-hidden="true">
        <circle cx="36" cy="36" r="36" fill="var(--navy)"/>
        <path d="M25 20c2-1.5 4-1 5 1l3 6c.8 1.6.3 3.2-1 4.2l-2 1.5c1.5 3.6 4.5 6.8 8 8.6l1.6-2c1-1.3 2.8-1.7 4.2-.9l6 3.2c1.8 1 2.2 3 .8 4.8-2.5 3.4-6 4.6-9.6 3.2-8.8-3.4-15.6-10.6-18.6-19.6-1.2-3.6.2-7.4 2.6-10z" fill="var(--white)"/>
        <path d="M40 22a12 12 0 0 1 10 10" stroke="var(--white)" stroke-width="2.6" fill="none" stroke-linecap="round"/>
        <path d="M40 15a19 19 0 0 1 17 17" stroke="var(--white)" stroke-width="2.6" fill="none" stroke-linecap="round"/>
      </svg>
      <span class="phone-band__number">(408)614-2907</span>
    </div>

    <div class="email">
      <svg class="email__icon" viewBox="0 0 34 26" aria-hidden="true">
        <rect x="1.5" y="1.5" width="31" height="23" fill="none" stroke="var(--medium)" stroke-width="3"/>
        <path d="M2 2l15 13L32 2M2 24l11-11M32 24L21 13" fill="none" stroke="var(--medium)" stroke-width="3"/>
      </svg>
      <span>info@bramblecresthomes.com</span>
    </div>

    <div class="license license--cadre">
      <span class="license__label">CADRE</span>
      <span class="license__number">#02794613</span>
    </div>
    <div class="license license--contractor">
      <span class="license__label">CONTRACTORS LICENSE</span>
      <span class="license__number">#1178524</span>
    </div>
  </main>
</body>
</html>
```